Hvac and insulation company needs good looking business card design

We are hvac and insulation company and looking for a new business cards that look to today standards designs

Target Market(s)

homeowners

Industry/Entity Type

Hvac

Contact Information for Business Card

Name: Walter Brinoku
Home comfort consultant
address: 4827 Dunmore St #215 Oakland, CA 94619
office: 888-316-2790
cell: 510-742-3185
Lic.# 584261
Email: walter@corvane-hvac.com
Web: corvane-hvac.com

Requirements
Must have
• clean and sleek look
Nice to have
• simple with a clean look
Should not have
• to busy business card

```html
<!DOCTYPE html>
<html lang="en">
<head>
<meta charset="UTF-8">
<title>Corvane Home Solutions — Business Card</title>
<link href="https://fonts.googleapis.com/css2?family=Rubik:wght@400;500;700&display=swap" rel="stylesheet">
<style>
  :root {
    --backdrop: #111111;
    --orange: #f28a2e;
    --orange-light: #f79a45;
    --slate: #6d6e72;
    --ink: #4a4a4f;
    --paper: #ffffff;
  }
  * { margin: 0; padding: 0; box-sizing: border-box; }
  html, body { width: 1200px; height: 1000px; overflow: hidden; }
  body {
    background: var(--backdrop);
    font-family: "Rubik", sans-serif;
    position: relative;
  }
  .card {
    position: absolute;
    left: 340px;
    width: 520px;
    height: 298px;
    border-radius: 18px;
    overflow: hidden;
  }
  /* Back side */
  .card-back {
    top: 170px;
    background: linear-gradient(120deg, var(--orange-light), var(--orange));
  }
  .back-brand {
    position: absolute;
    left: 0; right: 0; top: 104px;
    display: flex; align-items: center; justify-content: center; gap: 14px;
    color: var(--paper);
    font-weight: 700;
    font-size: 52px;
    letter-spacing: -0.5px;
  }
  .back-brand .brand-square {
    width: 30px; height: 30px; background: var(--paper);
  }
  .back-web {
    position: absolute;
    left: 36px; bottom: 30px;
    color: var(--paper);
    font-size: 17px;
    font-weight: 500;
  }
  /* Front side */
  .card-front {
    top: 530px;
    background: var(--paper);
  }
  .band-top {
    position: absolute; left: 0; top: 0;
    width: 170px; height: 26px;
    background: var(--slate);
    clip-path: polygon(0 0, 100% 0, 88% 100%, 0 100%);
  }
  .band-bottom {
    position: absolute; right: 0; bottom: 0;
    width: 300px; height: 24px;
    background: var(--orange);
    clip-path: polygon(0 0, 100% 0, 100% 100%, 8% 100%);
  }
  .brand {
    position: absolute; right: 34px; top: 58px;
    text-align: left;
  }
  .brand-name {
    display: flex; align-items: center; gap: 10px;
    color: var(--orange);
    font-weight: 700;
    font-size: 44px;
    line-height: 1;
  }
  .brand-name .brand-square { width: 20px; height: 20px; background: var(--orange); }
  .brand-tagline {
    margin-left: 30px;
    color: var(--slate);
    font-size: 14px;
    letter-spacing: 2.5px;
  }
  .person { position: absolute; left: 34px; top: 92px; }
  .person-name { color: var(--orange); font-size: 20px; font-weight: 500; }
  .person-title { color: var(--slate); font-size: 12px; font-weight: 700; margin-top: 1px; }
  .contacts { position: absolute; left: 34px; top: 152px; list-style: none; }
  .contacts li {
    display: flex; align-items: center; gap: 9px;
    color: var(--ink); font-size: 13px; margin-bottom: 7px;
  }
  .contacts svg { width: 12px; height: 12px; fill: var(--orange); flex: none; }
  .address {
    position: absolute; right: 34px; bottom: 42px;
    text-align: right; color: var(--ink); font-size: 14px; line-height: 1.4;
  }
</style>
</head>
<body>
  <section class="card card-back">
    <div class="back-brand"><span class="brand-square"></span>corvane</div>
    <div class="back-web">www.corvane-hvac.com</div>
  </section>

  <section class="card card-front">
    <div class="band-top"></div>
    <div class="band-bottom"></div>

    <div class="brand">
      <div class="brand-name"><span class="brand-square"></span>corvane</div>
      <div class="brand-tagline">home solutions</div>
    </div>

    <div class="person">
      <div class="person-name">Walter Brinoku</div>
      <div class="person-title">Director</div>
    </div>

    <ul class="contacts">
      <li>
        <svg viewBox="0 0 24 24" aria-hidden="true"><path d="M6.6 10.8a15 15 0 0 0 6.6 6.6l2.2-2.2a1 1 0 0 1 1-.25 11.4 11.4 0 0 0 3.6.57 1 1 0 0 1 1 1V20a1 1 0 0 1-1 1A17 17 0 0 1 3 4a1 1 0 0 1 1-1h3.5a1 1 0 0 1 1 1c0 1.25.2 2.45.57 3.57a1 1 0 0 1-.25 1z"/></svg>
        888-316-2790
      </li>
      <li>
        <svg viewBox="0 0 24 24" aria-hidden="true"><path d="M7 1h10a2 2 0 0 1 2 2v18a2 2 0 0 1-2 2H7a2 2 0 0 1-2-2V3a2 2 0 0 1 2-2zm0 3v14h10V4z"/></svg>
        510-742-3185
      </li>
      <li>
        <svg viewBox="0 0 24 24" aria-hidden="true"><path d="M2 5h20v14H2zm2 2v.5l8 5 8-5V7l-8 5z"/></svg>
        walter@corvane-hvac.com
      </li>
    </ul>

    <div class="address">4827 Dunmore St #215<br>Oakland, CA 94619</div>
  </section>
</body>
</html>
```